Tall Fern Roofing Business Card

Need a business card with the logo that was designed here

Contact Information for Business Card

Name, Title, Phone, Email, Website, Company name

```html
<!DOCTYPE html>
<html lang="en">
<head>
<meta charset="UTF-8">
<title>Tall Fern Roofing Business Card</title>
<link rel="stylesheet" href="https://fonts.googleapis.com/css2?family=Open+Sans:wght@400;700&display=swap">
<style>
  :root {
    --backdrop: #484848;
    --card-dark: #161616;
    --card-light: #ffffff;
    --brand-blue: #1f74c0;
    --text-light: #f2f2f2;
  }
  * { margin: 0; padding: 0; box-sizing: border-box; }
  html, body {
    width: 1200px; height: 801px; overflow: hidden;
    background: var(--backdrop);
    font-family: "Open Sans", Arial, sans-serif;
  }
  .canvas {
    position: relative; width: 1200px; height: 801px;
    display: flex; align-items: center; justify-content: center; gap: 48px;
  }
  .card {
    width: 525px; height: 300px; border-radius: 16px;
    position: relative; overflow: hidden;
    border-bottom: 4px solid var(--brand-blue);
    box-shadow: 0 14px 30px rgba(0,0,0,.35);
  }
  .card--back { background: var(--card-dark); }
  .card--front { background: var(--card-light); }

  .wordmark {
    display: flex; align-items: center; gap: 10px;
    font-weight: 700; color: var(--brand-blue);
  }
  .wordmark__square { background: var(--brand-blue); flex: none; }

  .card--back .wordmark {
    position: absolute; left: 36px; top: 128px; font-size: 25px;
  }
  .card--back .wordmark__square { width: 16px; height: 16px; }

  .divider {
    position: absolute; left: 300px; top: 40px; width: 2px; height: 220px;
    background: var(--brand-blue);
  }
  .contact {
    position: absolute; left: 322px; top: 46px; color: var(--text-light);
    font-size: 13px; line-height: 1.45;
  }
  .contact__name {
    color: var(--brand-blue); font-weight: 700; font-size: 20px;
    letter-spacing: .5px; line-height: 1.1;
  }
  .contact__title { margin-bottom: 16px; }
  .contact__address { margin-bottom: 16px; }
  .contact__row { display: flex; align-items: center; gap: 7px; }
  .contact__row svg { width: 12px; height: 12px; flex: none; }

  .card--front .wordmark {
    position: absolute; left: 0; right: 0; top: 124px;
    justify-content: center; font-size: 38px;
  }
  .card--front .wordmark__square { width: 24px; height: 24px; }
</style>
</head>
<body>
<main class="canvas">
  <section class="card card--back" aria-label="Business card back with contact details">
    <div class="wordmark"><span class="wordmark__square"></span><span>Tall Fern Roofing</span></div>
    <div class="divider"></div>
    <div class="contact">
      <p class="contact__name">DANA WHITFIELD</p>
      <p class="contact__title">Managing Director</p>
      <p class="contact__address">Your address, City<br>State, Zip 1234</p>
      <p class="contact__row">
        <svg viewBox="0 0 12 12"><path fill="#1f74c0" d="M2.5 1 4.3 3 3.4 4.3c.7 1.6 2.2 3.1 3.8 3.8L8.6 7l2 1.8-.9 1.7C5.5 10.7 1.1 6.4 1 2.2z"/></svg>
        <span>123 456 789</span>
      </p>
      <p class="contact__row">
        <svg viewBox="0 0 12 12"><rect x="1" y="2.5" width="10" height="7" fill="#1f74c0"/><path d="M1 2.5 6 6.5l5-4" fill="none" stroke="#161616" stroke-width="1"/></svg>
        <span>info@tallfernmail.com</span>
      </p>
      <p class="contact__row">
        <svg viewBox="0 0 12 12"><circle cx="6" cy="6" r="5" fill="none" stroke="#1f74c0" stroke-width="1.3"/><path d="M1 6h10M6 1c-2.5 3-2.5 7 0 10M6 1c2.5 3 2.5 7 0 10" fill="none" stroke="#1f74c0" stroke-width="1"/></svg>
        <span>www.yourwebsite.com</span>
      </p>
    </div>
  </section>

  <section class="card card--front" aria-label="Business card front with company name">
    <div class="wordmark"><span class="wordmark__square"></span><span>Tall Fern Roofing</span></div>
  </section>
</main>
</body>
</html>
```